Home Security Company Business Card

Looking for a eye catching business card that is non traditional and stands out but yet still looks professional. It should include all the pertinent information such as name, title, address, telephone, e-mail, website address should definitely stand out and then finally the logo.

Target Market(s)

Residential and Commercial accounts mostly upscale accounts

Industry/Entity Type

Security

Contact Information for Business Card

Name
Title
Address
Office #
Cell #
E-mail
Website

Font styles to use
Serif
Sans Serif

Requirements
Must have
• Logo, two sided color configuration
Nice to have
• You decide
Should not have
• There really aren't any.

```html
<!DOCTYPE html>
<html lang="en">
<head>
<meta charset="utf-8">
<title>Hartwell Security Systems Inc. – Business Card</title>
<link rel="stylesheet" href="https://fonts.googleapis.com/css2?family=Tinos&family=Source+Sans+3:wght@400;600;700&display=swap">
<style>
  :root {
    --backdrop: #000000;
    --card-light: #f3f3f3;
    --gold-light: #ecbd55;
    --gold: #e5b24a;
    --gold-deep: #d9a13f;
    --brand-red: #7a1414;
    --ink: #3a3a3a;
    --white: #ffffff;
  }
  * { margin: 0; padding: 0; box-sizing: border-box; }
  html, body {
    width: 1200px; height: 900px; overflow: hidden;
    background: var(--backdrop);
  }
  .canvas { position: relative; width: 1200px; height: 900px; }

  .card {
    position: absolute; top: 200px; width: 310px; height: 502px;
    overflow: hidden;
  }
  .card--front {
    left: 293px; background: var(--card-light);
    border-radius: 52px 0 52px 0;
  }
  .card--back {
    left: 613px;
    background: radial-gradient(ellipse at 45% 45%, var(--gold-light) 0%, var(--gold) 55%, var(--gold-deep) 100%);
    border-radius: 0 52px 0 52px;
  }

  .brand { font-family: "Tinos", serif; font-weight: 400; color: var(--brand-red); text-transform: uppercase; line-height: 1; }

  .front-brand {
    position: absolute; left: 62px; top: 72px;
    display: flex; align-items: center; gap: 14px;
  }
  .front-brand__mark { width: 70px; height: 70px; border-radius: 50%; background: var(--brand-red); flex: none; }
  .front-brand__name { display: block; font-size: 24px; letter-spacing: -0.3px; }
  .front-brand__tag { display: block; font-size: 11.5px; margin-top: 2px; letter-spacing: -0.2px; }

  .contact { position: absolute; left: 27px; top: 299px; font-family: "Source Sans 3", sans-serif; color: var(--ink); }
  .contact__name { font-size: 19px; font-weight: 700; color: var(--brand-red); letter-spacing: 0.2px; line-height: 24px; }
  .contact__title { font-size: 14.5px; line-height: 20px; }
  .contact__address { font-size: 14px; line-height: 16px; margin-top: 17px; }
  .contact__list { list-style: none; margin-top: 11px; font-size: 14px; }
  .contact__list li { display: flex; align-items: center; gap: 7px; height: 19px; }
  .contact__icon { width: 9px; height: 10px; fill: var(--brand-red); flex: none; }

  .back-brand { position: absolute; left: 0; right: 0; top: 238px; text-align: center; padding-left: 6px; }
  .back-brand__name { display: block; font-size: 41px; letter-spacing: -0.5px; }
  .back-brand__tag { display: block; font-size: 20.5px; margin-top: 1px; letter-spacing: -0.3px; }

  .website {
    position: absolute; left: 0; right: 0; top: 442px; text-align: center; padding-left: 28px;
    font-family: "Source Sans 3", sans-serif; font-weight: 700; font-size: 17px; color: var(--white);
  }
</style>
</head>
<body>
<main class="canvas">
  <section class="card card--front" aria-label="Card front">
    <div class="front-brand">
      <span class="front-brand__mark"></span>
      <p class="brand">
        <span class="front-brand__name">Hartwell</span>
        <span class="front-brand__tag">Security Systems Inc.</span>
      </p>
    </div>

    <div class="contact">
      <p class="contact__name">JOHN SMITH</p>
      <p class="contact__title">Managing Director</p>
      <p class="contact__address">1234, Address Goes Here<br>Country Name, 123456</p>
      <ul class="contact__list">
        <li>
          <svg class="contact__icon" viewBox="0 0 10 10" aria-hidden="true"><path d="M0 3.2C0 1.6 2 1 5 1s5 .6 5 2.2V4H7.4V3H2.6v1H0z M2 5h6l1.5 4h-9z"/></svg>
          555-214-0386
        </li>
        <li>
          <svg class="contact__icon" viewBox="0 0 10 12" aria-hidden="true"><path d="M2 0h6a1 1 0 0 1 1 1v10a1 1 0 0 1-1 1H2a1 1 0 0 1-1-1V1a1 1 0 0 1 1-1zm.6 1.4v7.6h4.8V1.4zM5 9.7a.8.8 0 1 0 0 1.6.8.8 0 0 0 0-1.6z"/></svg>
          555-214-0387
        </li>
        <li>
          <svg class="contact__icon" viewBox="0 0 10 8" aria-hidden="true"><path d="M0 0h10v8H0zM1 1l4 3.2L9 1z" fill-rule="evenodd"/></svg>
          info@hartwellsecure.com
        </li>
      </ul>
    </div>
  </section>

  <section class="card card--back" aria-label="Card back">
    <p class="brand back-brand">
      <span class="back-brand__name">Hartwell</span>
      <span class="back-brand__tag">Security Systems Inc.</span>
    </p>
    <p class="website">www.hartwellsecure.com</p>
  </section>
</main>
</body>
</html>
```